Korval Advise Business Cards

We need a business card design for Korval Advise (Logo Attached), a management consultancy specialized in brand & business building.

Design should be clean, smart and a touch of innnovation without being gimmicky.

The details on the card should be:
Name: Tomas Velduren
Title: Managing Director
Address: 42 Marlowe Pier, Tarn Vessel Tower, Singapore 073926
Tel: +6285927461082
email: tv@korvaladvise.example
website: korvaladvise.example

For further background on corporate identity, please check www.korvaladvise.example
Updates

Dear all,

Many thanks for the submissions so far! I gave feedback to those designs that I prefer at this stage.

Overall I see that my preference goes into the direction that 'less is more' and 'simple is beautiful'

Please create uniqueness and standout by the simplicity and attraction of the overall concept and design.

Many thanks and please shout incase of questions!

Tomas

Industry/Entity Type

Business

```html
<!DOCTYPE html>
<html lang="en">
<head>
<meta charset="utf-8">
<title>Korval Advise Business Cards</title>
<link rel="stylesheet" href="https://fonts.googleapis.com/css2?family=Open+Sans:wght@400;600;700&display=swap">
<style>
  :root {
    --orange: #ff6600;
    --charcoal: #4a4a4c;
    --ink: #3a3a3a;
    --paper: #ffffff;
    --backdrop: #ececec;
    --rule: #9a9a9a;
  }
  * { margin: 0; padding: 0; box-sizing: border-box; }
  html, body {
    width: 1174px; height: 1200px; overflow: hidden;
    background: var(--backdrop);
    font-family: "Open Sans", Arial, sans-serif;
  }
  .canvas { position: relative; width: 1174px; height: 1200px; }

  .card {
    position: absolute; width: 942px; height: 540px;
    border-radius: 27px; overflow: hidden;
  }
  .card--front { left: 47px; top: 38px; background: var(--paper); border: 1.5px solid #2b2b2b; }
  .card--back { left: 196px; top: 611px; background: var(--orange); }

  .brand {
    position: absolute; left: 0; right: 0; text-align: center;
    font-weight: 600; line-height: 1; letter-spacing: 0.01em;
  }
  .card--front .brand { top: 106px; font-size: 70px; color: var(--charcoal); }
  .card--back .brand { top: 196px; font-size: 80px; color: var(--paper); }

  .address {
    position: absolute; right: 500px; top: 244px; font-style: normal;
    text-align: right; font-size: 23px; line-height: 41px; color: var(--ink);
  }
  .divider {
    position: absolute; left: 465px; top: 245px; width: 1.5px; height: 138px;
    background: var(--rule);
  }
  .contacts {
    position: absolute; left: 492px; top: 230px;
    list-style: none; font-size: 23px; color: var(--ink);
  }
  .contacts li { display: flex; align-items: center; gap: 10px; height: 50px; }
  .contacts svg { width: 20px; height: 20px; flex: none; }

  .wave { position: absolute; left: 0; top: 0; width: 100%; height: 100%; }

  .person { position: absolute; left: 121px; top: 460px; color: var(--paper); text-align: center; }
  .person__name { font-size: 28px; font-weight: 700; line-height: 36px; }
  .person__title { font-size: 23px; font-weight: 400; line-height: 32px; }

  .web {
    position: absolute; left: 0; right: 0; top: 376px; text-align: center;
    color: var(--paper); font-size: 23px; letter-spacing: 0.22em;
  }
</style>
</head>
<body>
<main class="canvas">

  <section class="card card--front">
    <svg class="wave" viewBox="0 0 698 400" preserveAspectRatio="none" aria-hidden="true">
      <path fill="var(--charcoal)" d="M0,306 C150,296 330,318 470,362 C560,378 645,352 698,326 L698,350 C640,376 560,392 470,386 C340,344 160,320 0,325 Z"/>
      <path fill="var(--orange)" d="M0,337 C160,332 320,352 440,386 C480,396 520,400 560,400 L0,400 Z M560,400 C620,398 670,385 698,372 L698,400 Z"/>
    </svg>

    <div class="brand">Korval Advise</div>

    <address class="address">
      42 Marlowe Pier, Tarn<br>
      Vessel Tower<br>
      Singapore 073926
    </address>

    <div class="divider"></div>

    <ul class="contacts">
      <li>
        <svg viewBox="0 0 20 20" aria-hidden="true"><circle cx="10" cy="10" r="8.5" fill="none" stroke="var(--orange)" stroke-width="1.6"/><path d="M7 5.5l2 2-1 1.2c.6 1.4 1.5 2.3 2.8 2.8l1.2-1 2 2-1.4 1.6C9.5 13.8 6.2 10.5 5.8 7z" fill="var(--orange)"/></svg>
        <span>+6285927461082</span>
      </li>
      <li>
        <svg viewBox="0 0 20 20" aria-hidden="true"><rect x="2" y="5" width="16" height="11" rx="1.5" fill="var(--orange)"/><path d="M2.5 6l7.5 5.5L17.5 6" fill="none" stroke="#fff" stroke-width="1.5"/></svg>
        <span>tv@korvaladvise.example</span>
      </li>
      <li>
        <svg viewBox="0 0 20 20" aria-hidden="true"><g fill="none" stroke="var(--orange)" stroke-width="1.5"><circle cx="10" cy="10" r="8"/><ellipse cx="10" cy="10" rx="3.5" ry="8"/><path d="M2 10h16M3.5 6h13M3.5 14h13"/></g></svg>
        <span>www.korvaladvise.example</span>
      </li>
    </ul>

    <div class="person">
      <p class="person__name">Tomas Velduren</p>
      <p class="person__title">Managing Director</p>
    </div>
  </section>

  <section class="card card--back">
    <div class="brand">Korval Advise</div>
    <p class="web">www.korvaladvise.example</p>
  </section>

</main>
</body>
</html>
```